Business Card Design

I already have a company logo for my company. I have a logo for the manufacturer we represent. I want a professional business card design.

```html
<!DOCTYPE html>
<html lang="en">
<head>
<meta charset="utf-8">
<title>Beacon Guard Co — Business Card</title>
<link href="https://fonts.googleapis.com/css2?family=Montserrat:wght@400;500;700&display=swap" rel="stylesheet">
<style>
  :root {
    --backdrop: #3b3b3d;
    --gold: #8c6c14;
    --gold-dark: #4a3a14;
    --red: #d8262b;
    --ink: #222222;
    --paper: #ffffff;
    --grey: #d9d9d9;
    --black: #111111;
    --silver: #eeeeee;
  }
  * { box-sizing: border-box; margin: 0; padding: 0; }
  html, body {
    width: 1200px; height: 688px; overflow: hidden;
    background: var(--backdrop);
    font-family: "Montserrat", Arial, sans-serif;
  }
  .canvas { position: relative; width: 1200px; height: 688px; }
  .card {
    position: absolute; top: 195px;
    width: 520px; height: 298px;
    overflow: hidden;
  }
  .card--front {
    left: 50px;
    background: linear-gradient(170deg, var(--gold) 0%, var(--gold) 45%, var(--gold-dark) 100%);
    display: flex; align-items: center; justify-content: center;
  }
  .card--back { left: 630px; background: var(--paper); }

  .brand { display: flex; align-items: center; gap: 12px; white-space: nowrap; }
  .brand__mark { width: 22px; height: 22px; flex: none; }
  .brand__name {
    font-weight: 700; text-transform: uppercase; letter-spacing: 1px;
    line-height: 1.1;
  }
  .card--front .brand__mark { background: var(--silver); }
  .card--front .brand__name { color: var(--silver); font-size: 34px; }

  .card--back .brand {
    position: absolute; left: 28px; top: 140px; gap: 9px;
  }
  .card--back .brand__mark { background: var(--red); width: 14px; height: 14px; }
  .card--back .brand__name { color: var(--red); font-size: 16px; letter-spacing: 0.5px; }

  .contact {
    position: absolute; left: 292px; top: 62px;
    padding-left: 12px;
    border-left: 1.5px solid var(--red);
    color: var(--ink);
    white-space: nowrap;
  }
  .contact__name { color: var(--red); font-weight: 700; font-size: 21px; line-height: 1.1; }
  .contact__title { font-size: 11.5px; margin-top: 3px; }
  .contact__address { font-size: 11.5px; margin-top: 12px; line-height: 1.35; }
  .contact__list { list-style: none; margin-top: 12px; font-size: 11.5px; line-height: 1.55; }
  .contact__list li { display: flex; align-items: center; gap: 7px; }
  .contact__list svg { width: 10px; height: 10px; fill: var(--red); flex: none; }

  .stripe {
    position: absolute; left: 0; bottom: 0; width: 100%; height: 9px;
    display: flex;
  }
  .stripe span { height: 100%; }
  .stripe__grey { width: 28%; background: var(--grey); }
  .stripe__black { width: 32%; background: var(--black); }
  .stripe__red { width: 22%; background: var(--red); }
  .stripe__gold { width: 18%; background: var(--gold); }
</style>
</head>
<body>
<main class="canvas">
  <section class="card card--front" aria-label="Card front">
    <div class="brand">
      <span class="brand__mark"></span>
      <span class="brand__name">Beacon Guard Co</span>
    </div>
  </section>

  <section class="card card--back" aria-label="Card back">
    <div class="brand">
      <span class="brand__mark"></span>
      <span class="brand__name">Beacon Guard Co</span>
    </div>

    <div class="contact">
      <p class="contact__name">Daniel Reyes</p>
      <p class="contact__title">Managing Director</p>
      <p class="contact__address">2480 Larkin Ave<br>Denver, CO 80219</p>
      <ul class="contact__list">
        <li>
          <svg viewBox="0 0 10 10" aria-hidden="true"><path d="M1 3c0-1 1-2 4-2s4 1 4 2v1H7V3H3v1H1zM2 5h6l1 4H1z"/></svg>
          555.210.0148
        </li>
        <li>
          <svg viewBox="0 0 10 10" aria-hidden="true"><path d="M0 2h10v6H0z M0 2l5 3.5L10 2" fill="none" stroke="#d8262b" stroke-width="1.4"/></svg>
          info@beaconguardco.com
        </li>
        <li>
          <svg viewBox="0 0 10 10" aria-hidden="true"><circle cx="5" cy="5" r="4.5"/><path d="M0.5 5h9M5 0.5c-2 2.5-2 6.5 0 9M5 0.5c2 2.5 2 6.5 0 9" stroke="#fff" stroke-width="0.8" fill="none"/></svg>
          www.beaconguardco.com
        </li>
      </ul>
    </div>

    <div class="stripe" aria-hidden="true">
      <span class="stripe__grey"></span>
      <span class="stripe__black"></span>
      <span class="stripe__red"></span>
      <span class="stripe__gold"></span>
    </div>
  </section>
</main>
</body>
</html>
```